New web page, 2 companies on the one page

A new web page for an engineering consultancy and maintenance management company

Corlett & Associates is the parent company covering the design and consultancy
Valtrix Engineering is the Maintenance and Reliability company

Target Market(s)

Food & Beverage, ingredients Manufacturing
engineering managers

Coding

Coded - Design and coding required

Number of Pages Required

1 page

Font styles to use
Other font styles liked:
• Roboto

Colors
1861ab
85acd3
d0dfed
cee9f5

```html
<!DOCTYPE html>
<html lang="en">
<head>
<meta charset="utf-8">
<title>Valtrix Engineering – Maintenance &amp; Reliability</title>
<link rel="stylesheet" href="https://fonts.googleapis.com/css2?family=Orbitron:wght@700;900&family=Roboto:wght@300;400;500;700&display=swap">
<style>
:root{
  --navy:#0b1f5e;
  --navy-deep:#081645;
  --blue:#1861ab;
  --sky:#85acd3;
  --mist:#d0dfed;
  --ice:#e4edf6;
  --white:#ffffff;
  --ink:#1b1f2a;
  --grey:#5a6170;
  --black:#050505;
  --stage:#eef1f5;
}
*{box-sizing:border-box;margin:0;padding:0}
html,body{width:1200px;height:2812px;overflow:hidden;background:var(--stage)}
body{font-family:"Roboto",Arial,sans-serif;color:var(--ink)}
.page{position:absolute;left:184px;top:0;width:832px;height:2812px;overflow:hidden;background:var(--white);box-shadow:0 0 40px rgba(0,0,0,.18)}
.abs{position:absolute}
.display{font-family:"Orbitron",Arial,sans-serif;font-weight:900;letter-spacing:.5px}

/* header */
.site-header{left:0;top:0;width:832px;height:48px;background:var(--navy)}
.brand{display:flex;align-items:center;gap:6px;color:var(--white);font-family:"Roboto",sans-serif;font-weight:700;font-size:13px;letter-spacing:1px}
.brand-square{width:14px;height:14px;background:var(--sky)}
.nav-link{top:19px;color:var(--white);font-size:10px}
.nav-link.active{border-bottom:1px solid var(--white);padding-bottom:1px}
.follow{left:702px;top:11px;color:var(--white);font-size:9px}
.social-dots{display:flex;gap:5px;margin-top:4px}
.social-dots span{width:7px;height:7px;border-radius:50%;background:var(--white)}

/* hero */
.hero-photo{left:0;top:48px;width:832px;height:398px;background:linear-gradient(100deg,#3a4d74 0%,#58698e 35%,#6c86a3 55%,#7c8d56 72%,#4c5d7c 100%)}
.hero-shade{left:0;top:48px;width:832px;height:398px;background:linear-gradient(90deg,rgba(11,31,94,.55) 0%,rgba(11,31,94,.2) 55%,rgba(11,31,94,0) 100%)}
.hero-title{left:74px;top:186px;color:var(--white);line-height:1.05}
.hero-title .l1{font-size:31px}
.hero-title .l2{font-size:20.5px}
.hero-title .l3{font-size:21px}
.hero-text{left:76px;top:276px;width:340px;color:var(--white);font-size:10.5px;line-height:14px}
.btn-outline-light{left:76px;top:313px;width:107px;height:21px;background:var(--white);color:var(--navy);font-size:9.5px;font-weight:500;display:flex;align-items:center;justify-content:center;gap:8px}
.dots{left:394px;top:422px;display:flex;gap:6px}
.dots span{width:8px;height:8px;border-radius:50%;background:var(--white)}
.dots span.ring{background:none;border:1px solid var(--white)}

/* section heading */
.section-title{font-size:26px;color:var(--ink)}
.rule{display:flex;align-items:center;gap:4px}
.rule i{display:block;height:1px;background:var(--ink)}
.rule b{display:block;width:9px;height:9px;border-radius:50%;background:var(--blue);border:2px solid var(--sky)}
.light .rule i{background:var(--white)}
.center-x{left:0;width:832px;text-align:center;display:flex;flex-direction:column;align-items:center}

/* about */
.about-text{left:74px;top:579px;width:354px;font-size:9.3px;line-height:12.6px;color:var(--ink)}
.btn-solid{background:var(--navy);color:var(--white);font-size:9.5px;display:flex;align-items:center;justify-content:center}
.about-mark{left:515px;top:495px;width:198px;height:201px;display:flex;align-items:center;justify-content:center;gap:8px;background:linear-gradient(135deg,#d8e4f1,#8fa6c6);color:var(--navy);font-weight:700;font-size:22px;letter-spacing:2px}
.about-mark .brand-square{width:22px;height:22px;background:var(--navy)}

/* services */
.services-bg{left:0;top:754px;width:832px;height:560px;background:var(--ice)}
.service-card{width:229px;height:160px;overflow:hidden;color:var(--white);box-shadow:0 6px 14px rgba(8,22,69,.25)}
.service-card .label{position:absolute;left:0;right:0;bottom:14px;text-align:center;font-size:15px;font-weight:500;text-shadow:0 1px 3px rgba(0,0,0,.5)}
.service-card.featured{background:var(--navy)}
.service-card.featured .label{top:60px;bottom:auto}
.service-card.featured p{position:absolute;left:30px;right:30px;top:82px;text-align:center;font-size:8.5px;line-height:10px;color:#d7e0f2}

/* features */
.features-photo{left:0;top:0;width:832px;height:2812px}
.feature-item{width:160px;color:var(--white)}
.feature-item h4{font-size:11px;font-weight:700;margin-bottom:4px}
.feature-item p{font-size:7px;line-height:8.6px;color:#c7d2ea}
.emblem{left:330px;top:1419px;width:170px;height:170px;border-radius:50%;border:1px dashed rgba(255,255,255,.7);display:flex;align-items:center;justify-content:center}
.emblem-core{width:140px;height:140px;border-radius:50%;background:var(--white);display:flex;align-items:center;justify-content:center;gap:6px;color:var(--navy);font-weight:700;font-size:15px;letter-spacing:1.5px}
.emblem-core .brand-square{width:12px;height:12px;background:var(--blue)}
.btn-ghost{left:369px;top:1655px;width:86px;height:21px;border:1px solid var(--white);color:var(--white);font-size:9.5px;display:flex;align-items:center;justify-content:center}

/* reviews */
.review-card{width:200px;height:255px;background:var(--white);box-shadow:0 4px 14px rgba(0,0,0,.12);overflow:hidden}
.review-card .base{position:absolute;left:0;right:0;bottom:0;height:92px;background:var(--navy)}
.review-card .quote{position:absolute;left:26px;top:10px;font-family:Georgia,serif;font-size:30px;font-weight:700;color:var(--navy)}
.review-card p{position:absolute;left:28px;right:28px;top:54px;text-align:center;font-size:7.4px;line-height:10.4px;color:var(--grey)}
.avatar{position:absolute;left:72px;top:135px;width:56px;height:56px;border-radius:50%;background:linear-gradient(160deg,#c9cdd5,#7e8594);border:2px solid var(--white)}
.review-card .name{position:absolute;left:0;right:0;top:212px;text-align:center;color:var(--white);font-size:8.5px;font-weight:500}
.review-card .social-dots{position:absolute;left:0;right:0;top:234px;justify-content:center}

/* contact */
.contact-left{left:0;top:2233px;width:424px;height:324px;background:var(--white)}
.contact-right{left:424px;top:2233px;width:408px;height:324px;background:var(--navy)}
.touch-title{left:59px;top:2284px;font-size:19px;font-weight:300;color:var(--ink)}
.touch-sub{left:59px;top:2317px;font-size:9px;color:var(--ink)}
.contact-line{left:72px;display:flex;align-items:center;gap:14px;font-size:8.5px;line-height:10px;color:var(--grey)}
.contact-line svg{flex:none}
.field{left:507px;width:249px;border:1px solid #8fa2cc;color:#c3cde5;font-size:8.5px;padding:4px 12px}
.btn-submit{left:507px;top:2485px;width:249px;height:23px;background:var(--white);color:var(--navy);font-size:9.5px;display:flex;align-items:center;justify-content:center;gap:30px}

/* footer */
.site-footer{left:0;top:2557px;width:832px;height:226px;background:var(--black);color:var(--white)}
.footer-brand{left:55px;top:2613px;font-size:24px}
.footer-brand .brand-square{width:26px;height:26px}
.footer-text{left:57px;top:2668px;width:212px;font-size:7.6px;line-height:10.5px;color:#c8c8c8}
.footer-head{top:2610px;font-size:9px;font-weight:700;letter-spacing:.4px}
.footer-list{list-style:none;font-size:8.3px;line-height:17px;color:#e5e5e5}
.footer-list li::before{content:"";display:inline-block;width:4px;height:4px;border-radius:50%;background:var(--white);margin-right:9px;vertical-align:middle}
.footer-email{left:678px;top:2649px;width:76px;height:14px;background:var(--white);color:var(--grey);font-size:7.5px;padding:2px 5px}
.copyright{left:0;top:2783px;width:832px;height:29px;background:var(--black);border-top:1px solid #333;color:#cfcfcf;font-size:8px;display:flex;align-items:center;justify-content:center}
</style>
</head>
<body>
<div class="page">

  <!-- header -->
  <header class="abs site-header">
    <div class="abs brand" style="left:76px;top:16px"><span class="brand-square"></span>VALTRIX</div>
    <a class="abs nav-link active" style="left:385px">Home</a>
    <a class="abs nav-link" style="left:433px">About</a>
    <a class="abs nav-link" style="left:487px">Services</a>
    <a class="abs nav-link" style="left:551px">Reviews</a>
    <a class="abs nav-link" style="left:618px">Contact</a>
    <div class="abs follow">Follow Us:<div class="social-dots"><span></span><span></span><span></span></div></div>
  </header>

  <!-- hero -->
  <section class="hero">
    <div class="abs hero-photo" role="img" aria-label="Engineer in hard hat and high-visibility jacket checking equipment in a food processing plant"></div>
    <div class="abs hero-shade"></div>
    <h1 class="abs display hero-title">
      <div class="l1">MANUFACTURING</div>
      <div class="l2">ENGINEERING SUPPORT</div>
      <div class="l3">ORGANISATION</div>
    </h1>
    <p class="abs hero-text">Lorem ipsum dolor sit amet, consectetur adipiscing elit. Scelerisque pellentesque sollicitudin diam vitae consectetur est sit.</p>
    <a class="abs btn-outline-light">Learn More
      <svg width="16" height="8" viewBox="0 0 16 8"><path d="M0 4h14M11 1l3 3-3 3" fill="none" stroke="currentColor" stroke-width="1.2"/></svg></a>
    <div class="abs dots"><span class="ring"></span><span></span><span></span><span></span></div>
    <svg class="abs" style="left:0;top:446px" width="832" height="32"><polygon points="0,0 832,0 0,30" fill="var(--navy)"/></svg>
  </section>

  <!-- about -->
  <section class="about">
    <div class="abs" style="left:81px;top:520px">
      <h2 class="display section-title">ABOUT US</h2>
      <div class="rule" style="margin-top:6px;margin-left:2px"><i style="width:60px"></i><b></b><i style="width:60px"></i></div>
    </div>
    <p class="abs about-text">Corlett &amp; Associates is specialised manufacturing engineering support organisation that can provide fast, nimble, and flexible services. We have a proven track record in delivering tangible outcomes in process design and fit-out, project management, manufacturing process and maintenance design and execution.Our specialist focus in food manufacturing across a range of sectors allows our team to deliver real benefits to performance and recognition of the clients investment</p>
    <a class="abs btn-solid" style="left:74px;top:671px;width:86px;height:21px">Read more</a>
    <div class="abs about-mark" role="img" aria-label="Valtrix Engineering brand panel with factory imagery"><span class="brand-square"></span>VALTRIX</div>
    <svg class="abs" style="left:0;top:722px" width="832" height="34"><polygon points="402,32 832,3 832,32" fill="var(--navy)"/></svg>
  </section>

  <!-- services -->
  <section class="services">
    <div class="abs services-bg"></div>
    <div class="abs center-x" style="top:795px">
      <h2 class="display section-title">SERVICES</h2>
      <div class="rule" style="margin-top:5px"><i style="width:70px"></i><b></b><i style="width:70px"></i></div>
    </div>

    <div class="abs service-card featured" style="left:65px;top:891px">
      <div class="label">Maintenance Execution</div>
      <p>Planned work, clear scope and reliable delivery across every shift on site.</p>
    </div>
    <div class="abs service-card" style="left:304px;top:891px;background:linear-gradient(150deg,#b59470,#e6ddd0 60%,#c8bba8)" role="img" aria-label="Tape measure resting on engineering plans">
      <div class="label">Major Equipment</div></div>
    <div class="abs service-card" style="left:543px;top:891px;background:linear-gradient(160deg,#8b95a4,#c9ced6 45%,#5b6574)" role="img" aria-label="Stainless steel process tanks in a plant">
      <div class="label">Process</div></div>
    <div class="abs service-card" style="left:65px;top:1061px;background:linear-gradient(150deg,#5d6b86,#b0743d 45%,#3a455c)" role="img" aria-label="Two engineers in hard hats reviewing a laptop on site">
      <div class="label">Project Managment</div></div>
    <div class="abs service-card" style="left:304px;top:1061px;background:linear-gradient(160deg,#1f2d3e,#2e5a48 45%,#1d2a44)" role="img" aria-label="Control room screens showing SCADA diagrams">
      <div class="label">SCADA</div></div>
    <div class="abs service-card" style="left:543px;top:1061px;background:linear-gradient(150deg,#b8b24e,#d89c54 45%,#7a7a8c)" role="img" aria-label="Industrial camera used for vision inspection">
      <div class="label">Vision Inspection System</div></div>
  </section>

  <!-- features -->
  <section class="features">
    <svg class="abs" style="left:0;top:1285px" width="832" height="470">
      <defs>
        <linearGradient id="featFill" x1="0" y1="0" x2="1" y2="1">
          <stop offset="0" stop-color="#15275f"/><stop offset=".5" stop-color="#0e2160"/><stop offset="1" stop-color="#0b1c55"/>
        </linearGradient>
      </defs>
      <polygon points="0,0 832,24 832,456 0,428" fill="url(#featFill)" role="img" aria-label="Faint background of an engineer at work in a plant"/>
    </svg>
    <div class="abs center-x light" style="top:1351px;color:var(--white)">
      <h2 class="display section-title" style="color:var(--white)">FEATURES</h2>
      <div class="rule" style="margin-top:5px"><i style="width:70px"></i><b></b><i style="width:70px"></i></div>
    </div>

    <svg class="abs" style="left:0;top:1400px" width="832" height="220">
      <g stroke="rgba(255,255,255,.55)" stroke-dasharray="3 3" fill="none">
        <line x1="236" y1="40" x2="296" y2="52"/>
        <line x1="236" y1="168" x2="296" y2="154"/>
        <line x1="596" y1="40" x2="536" y2="52"/>
        <line x1="596" y1="168" x2="536" y2="154"/>
      </g>
    </svg>

    <div class="abs feature-item" style="left:74px;top:1428px"><h4>Performance Measurement</h4><p>Track uptime, response and repair data on every line so teams can see trends early and act before small faults grow.</p></div>
    <div class="abs feature-item" style="left:74px;top:1557px"><h4>Performance Measurement</h4><p>Track uptime, response and repair data on every line so teams can see trends early and act before small faults grow.</p></div>
    <div class="abs feature-item" style="left:597px;top:1428px"><h4>Performance Measurement</h4><p>Track uptime, response and repair data on every line so teams can see trends early and act before small faults grow.</p></div>
    <div class="abs feature-item" style="left:597px;top:1557px"><h4>Performance Measurement</h4><p>Track uptime, response and repair data on every line so teams can see trends early and act before small faults grow.</p></div>

    <div class="abs emblem"><div class="emblem-core"><span class="brand-square"></span>VALTRIX</div></div>
    <a class="abs btn-ghost">View detail</a>
  </section>

  <!-- reviews -->
  <section class="reviews">
    <div class="abs center-x" style="top:1784px">
      <h2 class="display section-title">REVIEWS</h2>
      <div class="rule" style="margin-top:5px"><i style="width:70px"></i><b></b><i style="width:70px"></i></div>
    </div>

    <article class="abs review-card" style="left:88px;top:1882px">
      <div class="base"></div><div class="quote">&ldquo;</div>
      <p>Their engineers knew our plant quickly, cut downtime on the packing line and kept us informed at every single step.</p>
      <div class="avatar" role="img" aria-label="Reviewer portrait"></div>
      <div class="name">OWEN HARTLEY</div>
      <div class="social-dots"><span></span><span></span><span></span></div>
    </article>
    <article class="abs review-card" style="left:316px;top:1882px">
      <div class="base"></div><div class="quote">&ldquo;</div>
      <p>Their engineers knew our plant quickly, cut downtime on the packing line and kept us informed at every single step.</p>
      <div class="avatar" role="img" aria-label="Reviewer portrait"></div>
      <div class="name">OWEN HARTLEY</div>
      <div class="social-dots"><span></span><span></span><span></span></div>
    </article>
    <article class="abs review-card" style="left:545px;top:1882px">
      <div class="base"></div><div class="quote">&ldquo;</div>
      <p>Their engineers knew our plant quickly, cut downtime on the packing line and kept us informed at every single step.</p>
      <div class="avatar" role="img" aria-label="Reviewer portrait"></div>
      <div class="name">OWEN HARTLEY</div>
      <div class="social-dots"><span></span><span></span><span></span></div>
    </article>
  </section>

  <!-- contact -->
  <section class="contact">
    <svg class="abs" style="left:0;top:2203px" width="832" height="32"><polygon points="0,0 424,30 0,30" fill="var(--navy)"/></svg>
    <div class="abs contact-left"></div>
    <div class="abs contact-right"></div>
    <svg class="abs" style="left:402px;top:2268px" width="24" height="36"><polygon points="24,0 0,18 24,36" fill="var(--navy)"/></svg>

    <h3 class="abs touch-title">LETS GET IN TOUCH</h3>
    <p class="abs touch-sub">Lorem Ipsum Dolor Sit Amet, Consectetur Adipiscing Elit.Dolor Sit Amet</p>

    <div class="abs contact-line" style="top:2353px">
      <svg width="18" height="18" viewBox="0 0 24 24"><path d="M5 3h4l2 5-2.5 1.5a11 11 0 0 0 6 6L16 13l5 2v4a2 2 0 0 1-2 2A17 17 0 0 1 3 5a2 2 0 0 1 2-2z" fill="none" stroke="var(--navy)" stroke-width="1.4"/></svg>
      <div>0400 555 210<br>0400 555 211</div>
    </div>
    <div class="abs contact-line" style="top:2415px">
      <svg width="18" height="18" viewBox="0 0 24 24"><rect x="3" y="6" width="18" height="12" fill="none" stroke="var(--navy)" stroke-width="1.4"/><path d="M3 6l9 7 9-7" fill="none" stroke="var(--navy)" stroke-width="1.4"/></svg>
      <div>hello@valtrixeng<br>.example</div>
    </div>
    <div class="abs contact-line" style="top:2477px">
      <svg width="18" height="18" viewBox="0 0 24 24"><path d="M12 22s7-7 7-12a7 7 0 0 0-14 0c0 5 7 12 7 12z" fill="none" stroke="var(--navy)" stroke-width="1.4"/><circle cx="12" cy="10" r="2.5" fill="none" stroke="var(--navy)" stroke-width="1.4"/></svg>
      <div>48 Harbour Road<br>Brookvale 2100</div>
    </div>
    <svg class="abs" style="left:336px;top:2472px" width="28" height="28" viewBox="0 0 28 28"><circle cx="14" cy="14" r="12.5" fill="none" stroke="var(--navy)" stroke-width="1.4"/><path d="M7 15l14-7-5 14-3-5z" fill="var(--navy)"/></svg>

    <div class="abs center-x light" style="left:424px;width:408px;top:2276px;color:var(--white)">
      <h2 class="display" style="font-size:15px;color:var(--white)">CONTACT US</h2>
      <div class="rule" style="margin-top:6px"><i style="width:44px"></i><b style="width:7px;height:7px"></b><i style="width:44px"></i></div>
    </div>
    <div class="abs field" style="top:2331px;height:32px">Your Name</div>
    <div class="abs field" style="top:2373px;height:31px">Email Address</div>
    <div class="abs field" style="top:2414px;height:56px">Comments</div>
    <a class="abs btn-submit">Submit Now
      <svg width="34" height="8" viewBox="0 0 34 8"><path d="M0 4h32M29 1l3 3-3 3" fill="none" stroke="currentColor" stroke-width="1"/></svg></a>
  </section>

  <!-- footer -->
  <footer>
    <div class="abs site-footer"></div>
    <div class="abs brand footer-brand"><span class="brand-square"></span>VALTRIX</div>
    <p class="abs footer-text">Maintenance and reliability support for food, beverage and ingredient plants, built on practical engineering and steady long term partnerships.</p>

    <h5 class="abs footer-head" style="left:351px;color:var(--white)">QUICK LINKS</h5>
    <ul class="abs footer-list" style="left:351px;top:2632px">
      <li>Home</li><li>About us</li><li>Services</li><li>Conatct</li>
    </ul>

    <h5 class="abs footer-head" style="left:467px;color:var(--white)">SERVICES</h5>
    <ul class="abs footer-list" style="left:467px;top:2632px">
      <li>Process &amp; Facilities Design</li>
      <li>Project Management</li>
      <li>Major Equipment and Services</li>
      <li>Contact</li>
      <li>Engineering &amp; Maintenance Management</li>
      <li>Maintenance Execution</li>
      <li>Manufacturing Performance Measurement</li>
      <li>SCADA</li>
    </ul>

    <h5 class="abs footer-head" style="left:679px;color:var(--white)">SOCIAL LINKS</h5>
    <div class="abs social-dots" style="left:683px;top:2628px"><span></span><span></span><span></span><span></span></div>
    <div class="abs footer-email">email
      <svg style="position:absolute;right:6px;top:3px" width="9" height="8" viewBox="0 0 9 8"><path d="M0 4l9-4-2 8-2-3z" fill="none" stroke="var(--grey)" stroke-width=".8"/></svg></div>

    <div class="abs copyright">&copy; 2021 Valtrix Associates Pty Ltd. All rights reserved.</div>
  </footer>

</div>
</body>
</html>
```